COMPANY NAME: Bright Harbor Ventures: Task Description: We are a new UK based business with global rea

Target Market

- Personal and professional development – 30-55 age group, corporate leaders, Eastern European and Asian markets
- On-assignment projects – Corporate market – Eastern European and Asian Markets
- Property investment - 35-65 age group, Europe, USA, Australia

What we need

We need logos and brand design for a suite of web platforms (website, twitter and Facebook profile). We would like to have a cohesive and consistent look across all of our online platforms. The design suite must therefore include social media logos, backgrounds and headers. Specifically we are looking for:

a. Facebook header/page design: likely to have a more youthful look

b. Website: Header, background and layout that is responsive to devices, iPhone primarily, then tablet, then PC (we have purchased a website building package from SiteKettle so if you are familiar with one of their themes, it would be great to have a design that fits with a theme you would recommend); Design should be able to accommodate a place to position video in the medium term but an image in the short term.

c. LinkedIn: header/logo; more corporate look

d. Twitter: background/logo

e. Powerpoint template: background and logo - simple and soft background not busy

f. Electronic Newsletter: logo, header and sidebar; simple and soft background not busy

h. Business card: sophisticated and simple

Colors

We have in mind a preference for colors from the purple family, maybe lavender, so as to appeal to all genders and age groups. Though we are happy to go with a recommendation if you think otherwise.

We would like a look that is professional, airy, bright, fresh, futuristic, insightful, friendly.

Ethos of the brand

- experiencing opportunity and being fulfilled in a changing world
- services are facilitated through insights
- support provided through our product, services and tailored approach to coaching/partnerships (which includes private client match-making)
- we are service providers and passionate about quality and modern leadership skills at all stages in life.

The company name is "Bright Harbor Ventures” - our main message is helping people move to the next level - through investments, personal and professional growth.

Some of our messaging

1. International Leadership in a new world.

2. New technology;

3. Informed;

4. Positively Influential

5. Making a difference;

6. Empowered;

7. Risk free investments;

8. Commercial opportunity;

9. Fulfilled living;

10. Carefree and Fun Living;

11. Progression;

12. Open-minded

13. Energy/dynamic

The Business:
The business is to move people very quickly out of situations that hold them back. the situations could be their own personal situations; their career; their jobs; their teams; their ideas; their finances; their financial opportunities. Remove their fears and give them the strategies to take action. The team are international and have 40 years experience between them in this area.

We do want to come across modern and dynamic, customer outcome focussed, building long-term relationships; international.
Updates

Project Deadline Extended
Reason: We have not found the right designs - we are not just looking for a website design but also images and logos. Most images we can see in the designs are stock images - very standard. We need an image which will be the face of the company, like the shop front window. This main image will be used on social media (top image) and also the home page of the website.

Target Market(s)

30-55 years
Eastern Europe; UK; Asia; Africa; Middle East
Personal, Professional, Corporate, and Financial Growth

Industry/Entity Type

Business Service

Contact Information for Business Card

Simple and stylish
the 3 areas of the business on the reverse -

International look - Offices in UK and San Francisco

Company name
web address www.brightharborventure.com
email director@brightharborventure.com
Facebook bright harbor venture
LinkedIn Bright Harbor Venture
Twitter Bright Harbor Venture
Telephone: +44 (0) 768 213 5597

Logo Text

Something that symbolises unlimited growth - probably not text - could use the word INSIGHT in some way

Number of Pages Required

1 page

Colors
e4daeb
f3f1f8
ffffff

Requirements
Must have
• social media symbols and address
• company name
• Melanie Thorpe
• Director
• Telephone +44 (0) 768 213 5597
• Website name www.brightharborventure.co.uk
• Reverse of Card:
• Discreet, Fast, Bright Harbor Consultancy
• Corporate, Professional, Personal & Property Investment
Nice to have
• not too angular; soft lines; not too cluttered (possibly social media on the reverse and just logo, name, number on the front?
Should not have
• too busy

```html
<!DOCTYPE html>
<html lang="en">
<head>
<meta charset="utf-8">
<title>Bright Harbor Venture – Professional and Personal Consultancy</title>
<link href="https://fonts.googleapis.com/css2?family=Open+Sans:wght@300;400;600&display=swap" rel="stylesheet">
<style>
  :root {
    --lavender: #e4daeb;
    --mist: #f3f1f8;
    --white: #ffffff;
    --ink: #2f2c33;
    --text: #6b6670;
    --muted: #8a8590;
    --menu-bg: rgba(88, 82, 92, 0.92);
    --icon-disc-1: #ece6f0;
    --icon-disc-2: #cbbfd3;
    --icon: #5e5863;
    --footer-bar: #e6dfec;
    --font: "Open Sans", Arial, sans-serif;
  }
  * { box-sizing: border-box; margin: 0; padding: 0; }
  html, body { width: 1200px; height: 2532px; overflow: hidden; background: var(--white); }
  body { font-family: var(--font); color: var(--text); position: relative; }
  ul { list-style: none; }

  /* Hero */
  .hero { position: absolute; left: 0; top: 0; width: 1200px; height: 565px; overflow: hidden; }
  .hero-photo {
    position: absolute; inset: 0;
    background:
      radial-gradient(ellipse at 30% 40%, #d8cfc8 0%, rgba(216,207,200,0) 45%),
      radial-gradient(ellipse at 75% 60%, #b9d3e4 0%, rgba(185,211,228,0) 50%),
      linear-gradient(100deg, #8a9aa6 0%, #c9ccd2 35%, #dfe4ea 60%, #a9c6dc 100%);
  }
  .hero-veil { position: absolute; inset: 0; background: rgba(240, 240, 245, 0.25); }
  .brand { position: absolute; left: 111px; top: 34px; display: flex; align-items: center; gap: 10px; }
  .brand-mark { width: 46px; height: 46px; border-radius: 50%; background: var(--ink); }
  .brand-name { font-size: 20px; font-weight: 600; line-height: 24px; color: var(--ink); text-transform: uppercase; letter-spacing: 0.5px; }
  .menu-button {
    position: absolute; left: 991px; top: 34px; width: 98px; height: 50px;
    background: var(--menu-bg); color: var(--white);
    display: flex; align-items: center; justify-content: center; gap: 10px;
    font-size: 13px; text-transform: uppercase;
  }
  .menu-panel {
    position: absolute; left: 923px; top: 95px; width: 166px; height: 278px;
    background: var(--menu-bg); padding-top: 22px;
  }
  .menu-panel li {
    color: var(--white); font-size: 13px; text-transform: uppercase;
    text-align: right; padding-right: 27px; height: 41px; line-height: 30px;
  }
  .hero-rule { position: absolute; left: 287px; width: 743px; height: 1px; background: rgba(255,255,255,0.55); }
  .hero-title {
    position: absolute; left: 0; top: 380px; width: 1200px; text-align: center;
    font-size: 37px; font-weight: 300; color: var(--ink); text-transform: uppercase; letter-spacing: 0.5px;
  }
  .slider-dots { position: absolute; left: 587px; top: 529px; display: flex; gap: 8px; }
  .slider-dots span { width: 8px; height: 8px; border-radius: 50%; background: rgba(255,255,255,0.7); }
  .slider-dots span.is-active { background: var(--ink); }

  /* Section headings */
  .section-title {
    position: absolute; left: 0; width: 1200px; text-align: center;
    font-size: 30px; font-weight: 300; color: var(--ink); text-transform: uppercase;
  }

  /* Welcome */
  .welcome-lead { position: absolute; top: 714px; left: 0; width: 1200px; text-align: center; font-size: 17px; color: var(--ink); }
  .welcome-body {
    position: absolute; top: 753px; left: 138px; width: 929px; text-align: center;
    font-size: 12px; line-height: 26px; color: var(--text);
  }

  /* Features */
  .features-band { position: absolute; left: 0; top: 942px; width: 1200px; height: 498px; background: var(--lavender); }
  .watch-video {
    position: absolute; top: 1048px; left: 0; width: 1200px;
    display: flex; justify-content: center; align-items: center; gap: 10px;
    font-size: 16px; color: var(--ink);
  }
  .video-frame {
    position: absolute; left: 182px; top: 1104px; width: 834px; height: 446px;
    background: var(--white); padding: 4px;
    box-shadow: 0 14px 22px rgba(60, 50, 70, 0.25);
  }
  .video-still {
    width: 100%; height: 100%; position: relative;
    background:
      radial-gradient(ellipse at 45% 55%, #b48f78 0%, rgba(180,143,120,0) 30%),
      linear-gradient(90deg, #dfe8e3 0%, #c8d8d2 45%, #b6c4c4 70%, #2a3040 88%, #e4eaea 100%);
  }
  .play-button { position: absolute; left: 375px; top: 183px; }

  /* Services */
  .services { position: absolute; top: 1733px; left: 0; width: 1200px; }
  .service { position: absolute; top: 0; }
  .service-icon {
    width: 132px; height: 132px; border-radius: 50%;
    background: radial-gradient(circle at 50% 30%, var(--icon-disc-1) 0%, var(--icon-disc-2) 100%);
    display: flex; align-items: center; justify-content: center;
  }
  .service-title { margin-top: 24px; font-size: 19px; font-weight: 400; color: var(--ink); text-transform: uppercase; }
  .service-list { margin-top: 14px; }
  .service-list li { font-size: 12.5px; color: var(--text); height: 34px; display: flex; align-items: center; gap: 10px; }
  .service-list li::before { content: "»"; font-size: 13px; color: var(--muted); }

  /* Footer */
  .footer { position: absolute; left: 0; top: 2132px; width: 1200px; height: 311px; background: var(--mist); }
  .footer-col { position: absolute; top: 48px; }
  .footer-heading { font-size: 19px; font-weight: 400; color: var(--ink); text-transform: uppercase; }
  .footer-text { margin-top: 18px; font-size: 11.5px; line-height: 25px; color: var(--text); }
  .contact-line { display: flex; align-items: center; gap: 16px; margin-top: 14px; font-size: 14px; font-weight: 600; color: var(--ink); }
  .contact-icon { width: 40px; height: 40px; border-radius: 50%; background: #dcd4e2; display: flex; align-items: center; justify-content: center; }
  .quick-links { margin-top: 16px; }
  .quick-links li { font-size: 11.5px; color: var(--text); height: 29px; line-height: 29px; }
  .signup-field {
    margin-top: 18px; width: 308px; height: 46px; background: var(--white);
    border: 1px solid #ddd6e3; position: relative;
    font-size: 11.5px; color: var(--muted); line-height: 44px; padding-left: 16px;
  }
  .signup-submit {
    position: absolute; right: 4px; top: 4px; width: 44px; height: 36px; background: #cfc4d7;
    display: flex; align-items: center; justify-content: center;
  }
  .footer-bar { position: absolute; left: 0; top: 2443px; width: 1200px; height: 89px; background: var(--footer-bar); }
  .copyright { position: absolute; left: 110px; top: 36px; font-size: 12px; color: var(--text); }
  .connect { position: absolute; left: 889px; top: 29px; display: flex; align-items: center; gap: 8px; font-size: 12px; color: var(--ink); }
  .connect-dot { width: 26px; height: 26px; border-radius: 50%; background: #4b4650; }
</style>
</head>
<body>

<header class="hero">
  <div class="hero-photo" role="img" aria-label="Photo of three smiling colleagues reviewing papers together in a bright office"></div>
  <div class="hero-veil"></div>

  <div class="brand">
    <span class="brand-mark"></span>
    <span class="brand-name">Bright Harbor<br>Venture</span>
  </div>

  <div class="menu-button">
    <svg width="16" height="12" viewBox="0 0 16 12" aria-hidden="true"><rect width="16" height="2" fill="#fff"/><rect y="5" width="16" height="2" fill="#fff"/><rect y="10" width="16" height="2" fill="#fff"/></svg>
    <span>Menu</span>
  </div>
  <nav class="menu-panel">
    <ul>
      <li>About You</li>
      <li>About Us</li>
      <li>Our Values</li>
      <li>Testimonials</li>
      <li>Social Media</li>
      <li>News Alert</li>
    </ul>
  </nav>

  <div class="hero-rule" style="top:338px"></div>
  <h1 class="hero-title">Professional and Personal Consultancy</h1>
  <div class="hero-rule" style="top:478px"></div>

  <div class="slider-dots"><span class="is-active"></span><span></span></div>
</header>

<section class="welcome">
  <h2 class="section-title" style="top:655px">Welcome to Bright Harbor Venture</h2>
  <p class="welcome-lead">Hello and welcome to the company that works with you on your terms.</p>
  <p class="welcome-body">If you seek an experienced and trusted partner to work with you on an assignment or simply want some strategies to move your personal or professional talents to the next level then you are in the right place. If you feel that the pace of change in business is so fast that to be an outstanding leader you should ensure you are brought up to speed regularly then you are in the right place. If you are hearing about the essential new leadership essentials and you are ready to hear how to adopt them into your life or business then you are at the right place. I am so convinced that you will be delighted with how fast you can make change happen.</p>
</section>

<section class="features">
  <div class="features-band"></div>
  <h2 class="section-title" style="top:990px">Our Features</h2>
  <div class="watch-video">
    <svg width="16" height="16" viewBox="0 0 16 16" aria-hidden="true"><circle cx="8" cy="8" r="8" fill="#2f2c33"/><path d="M6 4.5 L11.5 8 L6 11.5 Z" fill="#fff"/></svg>
    <span>Watch Our Video</span>
  </div>
  <div class="video-frame">
    <div class="video-still" role="img" aria-label="Video still of a hand touching a glowing screen of growth charts and data">
      <svg class="play-button" width="76" height="76" viewBox="0 0 76 76" aria-hidden="true">
        <circle cx="38" cy="38" r="36" fill="rgba(90,85,95,0.75)" stroke="rgba(255,255,255,0.6)" stroke-width="3"/>
        <path d="M30 24 L54 38 L30 52 Z" fill="#fff"/>
      </svg>
    </div>
  </div>
</section>

<section class="services-section">
  <h2 class="section-title" style="top:1641px">What We Do?</h2>
  <div class="services">
    <div class="service" style="left:110px">
      <div class="service-icon">
        <svg width="70" height="50" viewBox="0 0 70 50" aria-hidden="true">
          <path d="M4 18 L18 8 L30 14 L40 10 L52 8 L66 18 L60 28 L48 40 L40 44 L30 38 L18 30 Z" fill="#5e5863"/>
          <path d="M30 20 L42 30 M26 26 L38 36 M34 16 L46 24" stroke="#ddd5e3" stroke-width="2.5"/>
        </svg>
      </div>
      <h3 class="service-title">Consultancy</h3>
      <ul class="service-list">
        <li>Professional and Personal</li>
        <li>Next Generation Leaders (16-30)</li>
        <li>Consultation Options</li>
      </ul>
    </div>
    <div class="service" style="left:462px">
      <div class="service-icon">
        <svg width="64" height="56" viewBox="0 0 64 56" aria-hidden="true">
          <rect x="4" y="38" width="10" height="16" fill="#5e5863"/>
          <rect x="18" y="30" width="10" height="24" fill="#5e5863"/>
          <rect x="32" y="34" width="10" height="20" fill="#5e5863"/>
          <rect x="46" y="22" width="10" height="32" fill="#5e5863"/>
          <path d="M4 28 L22 14 L36 22 L54 6" stroke="#5e5863" stroke-width="4" fill="none"/>
          <path d="M46 4 L58 2 L56 14 Z" fill="#5e5863"/>
        </svg>
      </div>
      <h3 class="service-title">On Assignment</h3>
      <ul class="service-list">
        <li>Team Cohesion Strategy</li>
        <li>Go To Market Strategy</li>
        <li>Internationalisation Strategy</li>
      </ul>
    </div>
    <div class="service" style="left:797px">
      <div class="service-icon">
        <svg width="46" height="58" viewBox="0 0 46 58" aria-hidden="true">
          <rect x="2" y="2" width="42" height="54" fill="none" stroke="#5e5863" stroke-width="3"/>
          <rect x="9" y="9" width="28" height="4" fill="#5e5863"/>
          <rect x="9" y="17" width="28" height="2" fill="#5e5863"/>
          <rect x="9" y="22" width="28" height="2" fill="#5e5863"/>
          <rect x="9" y="27" width="28" height="2" fill="#5e5863"/>
          <rect x="9" y="35" width="16" height="14" fill="#5e5863"/>
          <path d="M28 43 L32 47 L38 38" stroke="#5e5863" stroke-width="2.5" fill="none"/>
        </svg>
      </div>
      <h3 class="service-title">Property: Private Client</h3>
      <ul class="service-list">
        <li>Promotion and cash-buyer matching</li>
        <li>Investment: high return projects</li>
        <li>Commercial: Hotels and Senior Housing</li>
        <li>Prestige Residential: US, Australia, UK</li>
      </ul>
    </div>
  </div>
</section>

<footer>
  <div class="footer">
    <div class="footer-col" style="left:110px; width:300px">
      <h4 class="footer-heading">Contact Us</h4>
      <p class="footer-text">Let's chat, if you want a non committal conversation get in touch by email or telephone.</p>
      <div class="contact-line" style="margin-top:20px">
        <span class="contact-icon"><svg width="14" height="14" viewBox="0 0 14 14" aria-hidden="true"><path d="M3 1 L5 4 L4 6 C5 8 6 9 8 10 L10 9 L13 11 L12 13 C7 13 1 7 1 2 Z" fill="#5e5863"/></svg></span>
        <span>+44 (0) 768 213 5597</span>
      </div>
      <div class="contact-line">
        <span class="contact-icon"><svg width="16" height="12" viewBox="0 0 16 12" aria-hidden="true"><rect x="1" y="1" width="14" height="10" fill="none" stroke="#5e5863" stroke-width="1.5"/><path d="M1 1 L8 7 L15 1" fill="none" stroke="#5e5863" stroke-width="1.5"/></svg></span>
        <span>Director@brightharborventure.com</span>
      </div>
    </div>
    <div class="footer-col" style="left:517px">
      <h4 class="footer-heading">Quick Links</h4>
      <ul class="quick-links">
        <li>About You</li>
        <li>About Us</li>
        <li>Our Values</li>
        <li>Testimonials</li>
        <li>Social Media</li>
        <li>News Alert</li>
      </ul>
    </div>
    <div class="footer-col" style="left:766px; width:310px">
      <h4 class="footer-heading">Signup Our Newsletter</h4>
      <p class="footer-text">Lorem ipsum dolor sit amet, consectetur adipiscing elit. Aliquam in feugiat magna. Proin eu semper sem, vel effi citur dolor. Donec non posuere mi.</p>
      <div class="signup-field">Email Address
        <span class="signup-submit"><svg width="14" height="12" viewBox="0 0 14 12" aria-hidden="true"><path d="M0 5 H9 V2 L14 6 L9 10 V7 H0 Z" fill="#4b4650"/></svg></span>
      </div>
    </div>
  </div>
  <div class="footer-bar">
    <p class="copyright">Copyrights © 2016 Bright Harbor Venture. All Right Reserved.</p>
    <div class="connect">
      <span>Connect Us :</span>
      <span class="connect-dot"></span>
      <span class="connect-dot"></span>
      <span class="connect-dot"></span>
      <span class="connect-dot"></span>
    </div>
  </div>
</footer>

</body>
</html>
```